Diverse, up-scale salon needs eye-catching, unique business cards.

We are looking for a unique business card design for our stylist but that can also be multi functional and used for appointment reminder and referrals. I will need a design in a format that I can modify names and titles going forward. In the past we have had a dark background with the logo on one side, and stylist and contact information on the other but we are open to all ideas. I have included our mission statement as well as branded colors below. The statement doesn't need to go on the card, it's just a reference for target market. We need space for the stylists name, title, instagram handle and then the salons phone number, website and address. I am also open to adding a spot for a qr code linked to the stylist instagram or the salon booking link.

primary brand colors:
#333333 #233415 #36502a #93874a #000000
Mission statement:
Vessolin Hair Studio, a high-end salon located in the lively Downtown Farmington, Michigan, is committed to providing exceptional services in a welcoming and relaxed environment to meet the needs of our diverse clientele.
Our salon specializes in contemporary custom haircuts, coloring, extensions, and barbering and beard grooming services. Our team of skilled stylists is passionate and inventive in their hair styling techniques. At the heart of our salon are values centered on quality, innovation, creativity, and above all, comfort. These core values are evident in every appointment across our customizable array of services.
Our goal is to establish a benchmark for exceptional hair care for every human.
Website: www.vessolinhairstudio.example
instagram: @vessolinhairstudio
address: 41782 Pelham Crest Rd, Farmington MI
phone: 248-613-4087

Industry/Entity Type

Hair Salon

Contact Information for Business Card

Stylist name, title, phone, instagram, website, address, (optional qr code)

Requirements
Should not have
• Does not need mission statement on the card.

```html
<!DOCTYPE html>
<html lang="en">
<head>
<meta charset="utf-8">
<title>Vessolin Hair Studio – Business Card</title>
<link href="https://fonts.googleapis.com/css2?family=Arimo:wght@400;700&display=swap" rel="stylesheet">
<style>
  :root {
    --backdrop: #1c1c1c;
    --card-white: #ffffff;
    --brand-gold: #93874a;
    --text-gray: #7a7a7a;
    --rule-gray: #8a8a8a;
    --band-gray: #878787;
  }
  * { margin: 0; padding: 0; box-sizing: border-box; }
  html, body {
    width: 1200px; height: 1059px; overflow: hidden;
    background: var(--backdrop);
    font-family: "Arimo", Arial, sans-serif;
  }
  .canvas { position: relative; width: 1200px; height: 1059px; }

  .card { position: absolute; overflow: hidden; box-shadow: 0 12px 30px rgba(0,0,0,.55); }
  .card-front { left: 258px; top: 89px; width: 689px; height: 393px; background: var(--card-white); }
  .card-back { left: 252px; top: 541px; width: 701px; height: 400px; background: var(--brand-gold); }

  .brand-mark {
    position: absolute; display: flex; flex-direction: column; align-items: center; justify-content: center;
    font-weight: 700; text-transform: uppercase; letter-spacing: 3px; text-align: center; line-height: 1.15;
  }
  .card-front .brand-mark { left: 461px; top: 56px; width: 180px; height: 150px; color: var(--brand-gold); font-size: 22px; }
  .card-back .brand-mark { left: 220px; top: 120px; width: 260px; height: 160px; color: var(--card-white); font-size: 30px; }

  .person-name {
    position: absolute; left: 40px; top: 201px;
    font-size: 21px; font-weight: 700; color: var(--brand-gold); letter-spacing: .2px;
  }
  .person-title {
    position: absolute; left: 40px; top: 220px;
    font-size: 18px; color: var(--text-gray);
  }
  .divider { position: absolute; left: 40px; top: 249px; width: 609px; height: 1.5px; background: var(--rule-gray); }

  .contact-list { position: absolute; left: 40px; top: 270px; list-style: none; }
  .contact-item { display: flex; align-items: center; height: 28px; font-size: 19px; color: var(--text-gray); }
  .contact-icon { width: 16px; height: 16px; margin-right: 10px; flex: none; }

  .address {
    position: absolute; right: 40px; top: 302px; text-align: right;
    font-size: 18.5px; line-height: 24px; color: var(--text-gray); font-style: normal;
  }
  .footer-band { position: absolute; left: 0; bottom: 0; width: 689px; height: 14px; }
</style>
</head>
<body>
<main class="canvas">
  <section class="card card-front" aria-label="Card front">
    <div class="brand-mark">Vessolin<br>Hair Studio</div>

    <h1 class="person-name">MARCUS DELANEY</h1>
    <p class="person-title">Manager</p>
    <div class="divider"></div>

    <ul class="contact-list">
      <li class="contact-item">
        <svg class="contact-icon" viewBox="0 0 16 16" aria-hidden="true">
          <path d="M4 2 L6.5 5 L5 6.6 Q6.5 9.5 9.4 11 L11 9.5 L14 12 L12.3 14 Q6 13.5 2 4 Z" fill="#93874a"/>
        </svg>
        248-613-4087
      </li>
      <li class="contact-item">
        <svg class="contact-icon" viewBox="0 0 16 16" aria-hidden="true">
          <circle cx="8" cy="8" r="6" fill="none" stroke="#93874a" stroke-width="2"/>
        </svg>
        @vessolinhairstudio
      </li>
      <li class="contact-item">
        <svg class="contact-icon" viewBox="0 0 16 16" aria-hidden="true">
          <g fill="none" stroke="#93874a" stroke-width="1.3">
            <circle cx="8" cy="8" r="6.5"/>
            <ellipse cx="8" cy="8" rx="3" ry="6.5"/>
            <line x1="1.5" y1="8" x2="14.5" y2="8"/>
            <line x1="2.5" y1="4.8" x2="13.5" y2="4.8"/>
            <line x1="2.5" y1="11.2" x2="13.5" y2="11.2"/>
          </g>
        </svg>
        www.vessolinhairstudio.example
      </li>
    </ul>

    <address class="address">41782 Pelham Crest Rd<br>Farmington MI</address>

    <svg class="footer-band" viewBox="0 0 689 14" preserveAspectRatio="none" aria-hidden="true">
      <polygon points="0,0 482,0 470,14 0,14" fill="#93874a"/>
      <polygon points="494,0 689,0 689,14 482,14" fill="#878787"/>
    </svg>
  </section>

  <section class="card card-back" aria-label="Card back">
    <div class="brand-mark">Vessolin<br>Hair Studio</div>
  </section>
</main>
</body>
</html>
```